Business Card Design

New business card design

Target Market(s)

Residential & Commercial Property Managers

Industry/Entity Type

Plumbing Services

Contact Information for Business Card

Name - Rowan Keddle, title - Director, Phone Number - 0431 286 517, email - rowan@tbk-plumbing.com.au, Company ABN - 73 215 904 386,

Font styles to use
Sans Serif

Colors
0054AA
0677BA
7BADD7
CADEEF
E8F1F8

```html
<!DOCTYPE html>
<html lang="en">
<head>
<meta charset="utf-8">
<title>TBK Plumbing Services – Business Cards</title>
<link href="https://fonts.googleapis.com/css2?family=Poppins:wght@300;400;500;600&display=swap" rel="stylesheet">
<style>
  :root {
    --backdrop: #232323;
    --card: #ffffff;
    --navy: #1d2530;
    --aqua: #29a8e0;
    --taupe: #7a6f66;
    --ink: #1a1a1a;
  }
  * { margin: 0; padding: 0; box-sizing: border-box; }
  html, body {
    width: 1200px;
    height: 780px;
    overflow: hidden;
    background: var(--backdrop);
    font-family: "Poppins", sans-serif;
  }
  .sheet {
    position: relative;
    width: 1200px;
    height: 780px;
  }
  .card {
    position: absolute;
    top: 240px;
    width: 520px;
    height: 300px;
    background: var(--card);
    border-radius: 22px;
    overflow: hidden;
  }
  .card--contact { left: 60px; }
  .card--brand { left: 620px; }

  /* brand name */
  .brand {
    display: flex;
    align-items: center;
    gap: 10px;
    color: var(--navy);
    font-weight: 400;
  }
  .brand__dot {
    flex: none;
    border-radius: 50%;
    background: var(--aqua);
  }
  .brand__name { line-height: 1.1; white-space: nowrap; }

  .card--contact .brand {
    position: absolute;
    left: 34px;
    top: 66px;
    width: 200px;
    font-size: 15px;
  }
  .card--contact .brand__dot { width: 10px; height: 10px; }

  .divider {
    position: absolute;
    left: 258px;
    top: 50px;
    width: 1px;
    height: 200px;
    background: var(--aqua);
  }
  .abn {
    position: absolute;
    left: 34px;
    bottom: 42px;
    font-size: 12px;
    font-weight: 300;
    color: var(--aqua);
    letter-spacing: 0.02em;
  }

  .person {
    position: absolute;
    left: 282px;
    top: 62px;
    right: 20px;
  }
  .person__name {
    font-size: 24px;
    line-height: 1.1;
    white-space: nowrap;
  }
  .person__first { color: var(--aqua); font-weight: 600; }
  .person__last { color: var(--taupe); font-weight: 300; }
  .person__title {
    font-size: 12px;
    font-weight: 500;
    color: var(--ink);
    margin-top: 2px;
  }
  .contacts {
    list-style: none;
    margin-top: 22px;
  }
  .contacts li {
    display: flex;
    align-items: center;
    gap: 8px;
    font-size: 11.5px;
    color: var(--ink);
    margin-bottom: 9px;
    white-space: nowrap;
  }
  .contacts svg { flex: none; width: 14px; height: 14px; }

  .card--brand .brand {
    position: absolute;
    left: 0;
    right: 0;
    top: 0;
    bottom: 0;
    justify-content: center;
    font-size: 34px;
    gap: 14px;
  }
  .card--brand .brand__dot { width: 20px; height: 20px; }
</style>
</head>
<body>
<main class="sheet">

  <section class="card card--contact" aria-label="Business card, contact side">
    <div class="brand">
      <span class="brand__dot"></span>
      <span class="brand__name">TBK Plumbing Services</span>
    </div>
    <div class="divider"></div>
    <p class="abn">ABN - 73 215 904 386,</p>

    <div class="person">
      <p class="person__name"><span class="person__first">Rowan</span> <span class="person__last">Keddle</span></p>
      <p class="person__title">Director</p>
      <ul class="contacts">
        <li>
          <svg viewBox="0 0 16 16" aria-hidden="true"><path fill="#29a8e0" d="M4 1.5l2.2 2.6-1.2 1.6c.8 1.8 2.2 3.2 4 4l1.6-1.2 2.6 2.2-1.4 2.3C6.7 12.8 3.2 9.3 1.7 4.2z"/></svg>
          <span>0431 286 517</span>
        </li>
        <li>
          <svg viewBox="0 0 16 16" aria-hidden="true"><rect x="1.5" y="3.5" width="13" height="9" rx="1" fill="#29a8e0"/><path d="M2 4.5l6 4.5 6-4.5" fill="none" stroke="#fff" stroke-width="1.2"/></svg>
          <span>rowan@tbk-plumbing.com.au</span>
        </li>
        <li>
          <svg viewBox="0 0 16 16" aria-hidden="true"><circle cx="8" cy="8" r="6.5" fill="#29a8e0"/><path d="M1.5 8h13M8 1.5c-2.5 3-2.5 10 0 13M8 1.5c2.5 3 2.5 10 0 13" fill="none" stroke="#fff" stroke-width="0.9"/></svg>
          <span>www.tbk-plumbing.com.au</span>
        </li>
      </ul>
    </div>
  </section>

  <section class="card card--brand" aria-label="Business card, brand side">
    <div class="brand">
      <span class="brand__dot"></span>
      <span class="brand__name">TBK Plumbing Services</span>
    </div>
  </section>

</main>
</body>
</html>
```